PixelMarrow Inc. Website & iPhone Apps Landing Pages

We need a web site design for our company. We develop software and do various consultant projects for our clients. Our products focus on the mobile platform, mainly the iPhone (business, games, social, etc.). We want to communicate that our software is simple and good as candy. The web pages should be fun to look at not loosing seriousness and credibility. Web 2.0 style and 960 grid system a must. We are opened to any overall site colour scheme suggestions (look at the sites we like below).

Must haves:
- Our logo should be seen on the site and look great on it :-) (preview attached below)
- Main home page and app landing page.
- Section links/tabs on the home page (home,apps,support,blog,contact,about)
- No text in images
- Style sheet

Looks we like:
- http://k7q3vxp9lrtwz.examplecdn.net/441_Site_Mock/final_large.jpg
- http://k7q3vxp9lrtwz.examplecdn.net/Deluxe_71_Drawn_Phone_Landing_Page/final.jpg
- http://grenmoor.com/
- http://lumbrel.ca/
- http://fairtwig.com/

Industry/Entity Type

Business

Requirements
Must have
• - Company logo should look great on pages.
• - Main home page and app landing page.
• - Section links/tabs on the home page (home,apps,support,blog,contact,about)
• - Web 2.0 style.
• - 960 grid system (12 col, 16 col).
• - Sliced ann optmized
• - Exported in all major formats (psd,ai,eps,png,jpeg,etc)
• - Style sheet
Should not have
• - Text in images

```html
<!DOCTYPE html>
<html lang="en">
<head>
<meta charset="utf-8">
<title>PixelMarrow Inc. – Home</title>
<link rel="stylesheet" href="https://fonts.googleapis.com/css2?family=Arimo:wght@400;700&family=Noto+Sans:wght@400;600&display=swap">
<style>
:root{
  --topbar:#3b3b3d;
  --hero-top:#2c3f58;
  --hero-bottom:#15233a;
  --red:#d0111b;
  --red-dark:#a80c14;
  --nav-top:#5e6064;
  --nav-bottom:#3a3c40;
  --panel:#f2f2f2;
  --strip:#e0dcdb;
  --ink:#333;
  --muted:#555;
  --white:#fff;
  --footer-top:#505256;
  --footer-bottom:#3a3b3e;
}
*{margin:0;padding:0;box-sizing:border-box}
html,body{width:981px;height:1200px;overflow:hidden;background:#fff}
body{position:relative;font-family:"Arimo",Arial,sans-serif;color:var(--ink)}
.abs{position:absolute}
.topbar{left:0;top:0;width:981px;height:67px;background:linear-gradient(#444548,var(--topbar));border-bottom:1px solid #222}
.brand{font-family:"Noto Sans",sans-serif;font-weight:600;font-size:28px;color:var(--red);display:flex;align-items:center;gap:8px}
.brand .dot{width:14px;height:14px;border-radius:50%;background:var(--red)}
.topbar .brand{left:113px;top:16px}
.contact{left:697px;top:19px;color:var(--white);font-weight:700;font-size:12.5px;line-height:16px}
.hero{left:0;top:67px;width:981px;height:356px;background:radial-gradient(ellipse at 60% 30%,#3a5070 0%,var(--hero-top) 35%,var(--hero-bottom) 100%)}
.hero h1{left:111px;top:66px;font-family:"Noto Sans",sans-serif;font-weight:400;font-size:31px;color:var(--white)}
.hero .rule{left:111px;top:109px;width:313px;height:1px;background:rgba(255,255,255,.35)}
.hero p{left:111px;top:130px;width:333px;font-size:10.5px;line-height:14.3px;color:#e6ebf2}
.btn-more{left:335px;top:217px;width:100px;height:31px;background:linear-gradient(#e4202a,var(--red-dark));border:1px solid #7a0a10;border-radius:3px;color:var(--white);font-family:"Noto Sans",sans-serif;font-size:16px;text-align:center;line-height:29px}
.dots{left:117px;top:258px;display:flex;gap:5px}
.dots span{width:7px;height:7px;border-radius:50%;background:#8b96a5}
.dots span:first-child{background:#fff}
.phones{left:644px;top:20px;width:152px;height:282px;border-radius:18px;background:linear-gradient(150deg,#3a3d44,#101216 60%,#2a2d33)}
.nav{left:111px;top:371px;width:749px;height:52px;background:linear-gradient(var(--nav-top),var(--nav-bottom));border-radius:3px 3px 0 0;display:flex}
.nav a{display:block;height:52px;line-height:52px;text-align:center;color:var(--white);text-decoration:none;font-size:14px;border-right:1px solid #2c2d30;box-shadow:1px 0 0 #6b6d71}
.nav a.current{font-weight:700;background:linear-gradient(#4d4f53,#333438)}
.panel{left:111px;top:423px;width:749px;height:297px;background:linear-gradient(var(--panel),#fafafa)}
.panel h2{left:17px;top:22px;font-family:"Noto Sans",sans-serif;font-weight:400;font-size:19px;color:#222}
.panel .intro{left:17px;top:53px;width:715px;font-size:10.5px;line-height:13.5px;color:var(--muted)}
.panel .rule{left:17px;top:106px;width:715px;height:1px;background:#d4d4d4}
.panel h3{left:17px;top:122px;font-family:"Noto Sans",sans-serif;font-weight:400;font-size:16.5px;color:#222}
.strip{left:32px;top:157px;width:686px;height:109px;background:var(--strip);border-radius:2px}
.arrow{width:22px;height:22px}
.app-card{top:11px;width:235px;height:90px}
.shot{background:linear-gradient(160deg,#2f4e7a,#18243a);border-radius:4px}
.app-card .shot{left:0;top:0;width:62px;height:90px}
.app-card .info{left:90px;top:0;width:110px;font-size:10px;line-height:14px;color:var(--muted)}
.label{color:var(--red)}
.app-card b{color:#333}
.read{left:145px;top:80px;width:39px;height:10px;background:var(--red);color:#fff;font-size:6px;line-height:10px;text-align:center;font-weight:700}
.feature{left:133px;width:460px;height:150px}
.feature .shot{left:0;top:0;width:128px;height:148px}
.feature h4{left:162px;top:0;font-family:"Noto Sans",sans-serif;font-weight:400;font-size:15.5px;color:#333}
.feature p{left:162px;top:21px;width:290px;font-size:10px;line-height:14px;color:var(--muted)}
.feature a{left:162px;top:125px;font-size:11px;color:var(--red);text-decoration:none}
.sidebar{left:608px;top:760px;width:253px;height:304px;background:linear-gradient(#ededed,#fafafa);border-radius:3px;box-shadow:0 3px 4px rgba(0,0,0,.12)}
.sidebar h4{left:22px;top:14px;font-family:"Noto Sans",sans-serif;font-weight:400;font-size:16px;color:#333}
.side-item{left:24px;width:215px;height:60px}
.side-item .shot{left:0;top:0;width:47px;height:59px}
.side-item p{left:61px;top:3px;width:150px;font-size:10px;line-height:14px;color:var(--muted)}
.side-item b{color:#333}
.footer{left:0;top:1091px;width:981px;height:109px;background:linear-gradient(var(--footer-top),var(--footer-bottom))}
.footer .brand{left:111px;top:40px;font-size:25px}
.social{left:683px;top:22px;display:flex;gap:14px}
.social span{width:23px;height:23px;border-radius:3px;background:#6f7985}
.copy{right:120px;top:83px;font-size:9.5px;color:#a7a9ad}
</style>
</head>
<body>
<header class="topbar abs">
  <div class="brand abs"><span class="dot"></span>PixelMarrow</div>
  <div class="contact abs">Call Us: 555-010-0199<br>Email:info@pixelmarrow.com</div>
</header>

<section class="hero abs">
  <h1 class="abs">Stylish applications</h1>
  <div class="rule abs"></div>
  <p class="abs">It is a long established fact that a reader will be distracted by the readable content of a page when looking at its layout. The point of using Lorem Ipsum is that it has a more-or-less normal distribution of letters, as opposed to using 'Content here, content here', making it look like readable English.</p>
  <div class="btn-more abs">More info</div>
  <div class="dots abs"><span></span><span></span><span></span><span></span></div>
  <div class="phones abs" role="img" aria-label="Two smartphones showing an app home screen"></div>
</section>

<nav class="nav abs">
  <a class="current" style="width:103px">Home</a>
  <a style="width:97px">Portfolio</a>
  <a style="width:103px">Blog</a>
  <a style="width:113px">Services</a>
  <a style="width:119px">About Us</a>
  <a style="width:131px">Contact Us</a>
</nav>

<main>
<section class="panel abs">
  <h2 class="abs">Welcome to Our Site</h2>
  <p class="intro abs">It is a long established fact that a reader will be distracted by the readable content of a page when looking at its layout. The point of using Lorem Ipsum is that it has a more-or-less normal distribution of letters, as opposed to using 'Content here, content here', making it look like readable English.</p>
  <div class="rule abs"></div>
  <h3 class="abs">Latest Applications</h3>
  <svg class="arrow abs" style="left:3px;top:198px" viewBox="0 0 22 22"><circle cx="11" cy="11" r="11" fill="#222"/><path d="M14 5 6 11l8 6z" fill="#fff"/></svg>
  <svg class="arrow abs" style="left:723px;top:198px" viewBox="0 0 22 22"><circle cx="11" cy="11" r="11" fill="#222"/><path d="M8 5l8 6-8 6z" fill="#fff"/></svg>
  <div class="strip abs">
    <div class="app-card abs" style="left:4px">
      <div class="shot abs" role="img" aria-label="App screenshot with blue home screen"></div>
      <div class="info abs"><span class="label">Name:</span> <b>APPs</b><br><span class="label">Description:</span><br>It is a long established fact that a reader will be distracted by the read</div>
      <div class="read abs">Read More</div>
    </div>
    <div class="app-card abs" style="left:250px">
      <div class="shot abs" style="background:linear-gradient(160deg,#7a2f8a,#1f1226)" role="img" aria-label="App screenshot with purple wallpaper"></div>
      <div class="info abs" style="left:91px"><span class="label">Name:</span> <b>APPs</b><br><span class="label">Description:</span><br>It is a long established fact that a reader will be distracted by the read</div>
      <div class="read abs">Read More</div>
    </div>
    <div class="app-card abs" style="left:486px">
      <div class="shot abs" style="background:linear-gradient(160deg,#a8501e,#2a1a12)" role="img" aria-label="App screenshot with orange cartoon wallpaper"></div>
      <div class="info abs" style="left:88px"><span class="label">Name:</span> <b>APPs</b><br><span class="label">Description:</span><br>It is a long established fact that a reader will be distracted by the read</div>
      <div class="read abs" style="left:152px">Read More</div>
    </div>
  </div>
</section>

<article class="feature abs" style="top:744px">
  <div class="shot abs" style="background:linear-gradient(#1b2f55,#6d7f95)" role="img" aria-label="Featured app screenshot with winter theme"></div>
  <h4 class="abs">Featured Application</h4>
  <p class="abs">It is a long established fact that a reader will be distracted by the readable content of a page when looking at its layout. The point of using Lorem Ipsum.content of a page when looking at its layout. The point of using Lorem Ipsum.The point of using Lorem Ipsum. The point of using Lorem Ipsum.content of a page when looking at its layout. The point of using Lorem Ipsum.The point of using Lorem Ipsum.The point of using Lorem Ipsum.</p>
  <a class="abs" href="#">Get quote/Detail info</a>
</article>
<article class="feature abs" style="top:905px">
  <div class="shot abs" style="background:linear-gradient(#2c6a9a,#0e2a44)" role="img" aria-label="Featured app screenshot with blue home screen"></div>
  <h4 class="abs">Featured Application</h4>
  <p class="abs">It is a long established fact that a reader will be distracted by the readable content of a page when looking at its layout. The point of using Lorem Ipsum.content of a page when looking at its layout. The point of using Lorem Ipsum.The point of using Lorem Ipsum. The point of using Lorem Ipsum.content of a page when looking at its layout. The point of using Lorem Ipsum.The point of using Lorem Ipsum.The point of using Lorem Ipsum.</p>
  <a class="abs" style="left:165px;top:136px" href="#">Get quote/Detail info</a>
</article>

<aside class="sidebar abs">
  <h4 class="abs">Latest Applications</h4>
  <div class="side-item abs" style="top:41px">
    <div class="shot abs" style="background:linear-gradient(160deg,#7a2f8a,#1f1226)" role="img" aria-label="App thumbnail with purple wallpaper"></div>
    <p class="abs"><b>It is a long established</b> fact that a reader will be distracted by the readable content of a page when looking at its layout.</p>
  </div>
  <div class="side-item abs" style="top:124px">
    <div class="shot abs" style="background:linear-gradient(160deg,#a8501e,#2a1a12)" role="img" aria-label="App thumbnail with orange wallpaper"></div>
    <p class="abs"><b>It is a long established</b> fact that a reader will be distracted by the readable content of a page when looking at its layout.</p>
  </div>
  <div class="side-item abs" style="top:203px">
    <div class="shot abs" style="background:linear-gradient(#1b2f55,#6d7f95)" role="img" aria-label="App thumbnail with winter theme"></div>
    <p class="abs"><b>It is a long established</b> fact that a reader will be distracted by the readable content of a page when looking at its layout.</p>
  </div>
</aside>
</main>

<footer class="footer abs">
  <div class="brand abs"><span class="dot"></span>PixelMarrow</div>
  <div class="social abs"><span></span><span></span><span></span><span></span><span></span></div>
  <div class="copy abs">Copyright © 2010 PixelMarrow. All Rights reserved</div>
</footer>
</body>
</html>
```